Pet Care Business Card

Dog & Cat Grooming, we come to you or come to Whisker Haven Grooming
Doggy day care,
Boutique holiday care,
Pet Supplies
All Natural Products used
Have created the logo, which I will forward shortly but need help to have it on flyers business cards ect
email whiskerhavengrooming@mailbrook.net
Ph: 0471352706
Colours: Green Black and paws prints nott sure what colour for them
Updates
Thank you to all that forwarded their designs, very hard choice and I thank you for your effort, shall recommend this to all my collegues
Thanks Again Dot :)
Industry/Entity Type
Business
Contact Information for Business Card
0471352706
517 upper Tindale Road
Brookvale QLD 4581

```html
<!DOCTYPE html>
<html lang="en">
<head>
<meta charset="utf-8">
<title>Whisker Haven Grooming – Business Card</title>
<link rel="stylesheet" href="https://fonts.googleapis.com/css2?family=Open+Sans:wght@400;600;700&display=swap">
<style>
  :root {
    --backdrop: #e9e7e3;
    --card: #ffffff;
    --accent: #1e7bd4;
    --ink: #2b2b2b;
    --ink-soft: #3a3a3a;
  }
  * { margin: 0; padding: 0; box-sizing: border-box; }
  html, body {
    width: 1200px; height: 959px; overflow: hidden;
    background: var(--backdrop);
    font-family: "Open Sans", Arial, sans-serif;
  }
  .card {
    position: absolute; left: 150px; top: 222px;
    width: 900px; height: 514px;
    background: var(--card);
    box-shadow: 0 10px 30px rgba(0,0,0,.18);
    overflow: hidden;
  }
  .tab {
    position: absolute; width: 34px; height: 112px;
    background: var(--accent); border-radius: 10px;
  }
  .tab--left { left: -14px; top: 220px; }
  .tab--right { right: -14px; top: 72px; }
  .brand {
    position: absolute; left: 70px; top: 222px; width: 330px;
    text-align: center; color: var(--accent);
    font-weight: 600; font-size: 30px; line-height: 1.15;
    letter-spacing: .5px;
  }
  .divider {
    position: absolute; left: 440px; top: 110px;
    width: 3px; height: 250px; background: var(--ink);
  }
  .contact { position: absolute; left: 470px; top: 100px; color: var(--ink); }
  .contact__name { font-weight: 700; font-size: 22px; letter-spacing: .3px; }
  .contact__role { font-size: 17px; color: var(--ink-soft); margin-top: 2px; }
  .contact__list { list-style: none; margin-top: 30px; }
  .contact__item {
    display: flex; align-items: center; gap: 12px;
    font-size: 19px; margin-bottom: 12px; color: var(--ink-soft);
  }
  .contact__icon {
    width: 22px; height: 22px; flex: none;
    background: var(--ink); border-radius: 50%;
    display: flex; align-items: center; justify-content: center;
  }
  .contact__item--small { font-size: 16px; }
</style>
</head>
<body>
  <div class="card">
    <div class="tab tab--left"></div>
    <div class="tab tab--right"></div>

    <div class="brand">Whisker Haven<br>Grooming</div>

    <div class="divider"></div>

    <div class="contact">
      <div class="contact__name">TOM ASHGROVE</div>
      <div class="contact__role">Managing Director</div>
      <ul class="contact__list">
        <li class="contact__item">
          <span class="contact__icon">
            <svg width="12" height="14" viewBox="0 0 12 14"><path d="M6 0a5 5 0 0 0-5 5c0 3.5 5 9 5 9s5-5.5 5-9a5 5 0 0 0-5-5zm0 7a2 2 0 1 1 0-4 2 2 0 0 1 0 4z" fill="#fff"/></svg>
          </span>
          517 upper Tindale Road
        </li>
        <li class="contact__item">
          <span class="contact__icon">
            <svg width="12" height="12" viewBox="0 0 12 12"><path d="M2.5 1l2 2.2-1 1.3a7 7 0 0 0 4 4l1.3-1L11 9.5 9.8 11C5 11 1 7 1 2.2z" fill="#fff"/></svg>
          </span>
          0471352706
        </li>
        <li class="contact__item contact__item--small">
          <span class="contact__icon">
            <svg width="12" height="10" viewBox="0 0 12 10"><rect x="0.5" y="1" width="11" height="8" rx="1" fill="#fff"/><path d="M1 1.5l5 4 5-4" stroke="#2b2b2b" stroke-width="1.2" fill="none"/></svg>
          </span>
          whiskerhavengrooming@mailbrook.net
        </li>
        <li class="contact__item">
          <span class="contact__icon">
            <svg width="14" height="14" viewBox="0 0 14 14" fill="none" stroke="#fff" stroke-width="1.2"><circle cx="7" cy="7" r="5.5"/><ellipse cx="7" cy="7" rx="2.3" ry="5.5"/><path d="M1.5 7h11M2.5 4h9M2.5 10h9"/></svg>
          </span>
          www.whiskerhaven.net
        </li>
      </ul>
    </div>
  </div>
</body>
</html>
```